Wordpress Theme for Medical Clinics

** Please view updated Sitemap2.pdf doc to clarify some confusion ***

This is a multiuser WordPress subscription site for medical clinics. Please see attachment for sitemap. Please do not include extra content like social media icons, search bars, or images. If you have questions, please ask for clarification.
The site contains the following pages and sub-pages:

1. Home
2. Our Clinic
2a. Our Clinic > Mission
2b. Our Clinic > Services
2c. Our Clinic > Clinic Policies
2d. Our Clinic > Schedules
3. Our Staff
3a. Our Staff > [Staff member page]
4. Resources
4a. Resources > Patient Health (index)
4b. Resources > Patient Health (index) > [post]
4c. Resources > Links
4d. Resources > Forms
5. Alerts
5a. Alerts > [Alert Page]
6. Contact Us

Includes the Following Pages, Subpages, and Content
1. Home
a. About Us
b. Our Staff
c. Bulletins
d. Accepting New Patients (shown as an alert widget)
e. Links
i. Physician Toolbox
ii. Book an Appointment
f. Clinic Policies
i. Show first 3 policies (e.g. Late Arrivals, Missed Appointments, Fees)
ii. Link to Clinic Policies page
g. Primary widget (displayed on all pages)
i. Hours of operation
ii. Contact Info
1. Tel
2. Fax
3. Email
4. Address
5. Get directions (link to Google Maps)
2. Our Clinic
a. Main Page
i. Clinic Name
ii. Overview
iii. Languages Spoken
iv. Secondary Navigation
1. Mission
2. Services
3. Clinic Policies
4. Schedules (see attachment)
b. Our Clinic > Mission
c. Our Clinic > Services
i. For each service include service TITLE and DESCRIPTION
d. Our Clinic > Clinic Policies
i. For each policy include policy TITLE and DESCRIPTION
ii. Include the following policies in mockup
1. Late arrivals
2. Missed appointments
3. Fees for missed appointments
4. Referrals and follow-ups
5. Services not covered by RDA
6. Information for LTF patients
7. Medical Legal Reports
e. Our Clinic > Schedules
3. Our Staff
a. Main Page
i. Display a list of staff members. Include NAME and DESIGNATION
b. Our Staff > [Staff Name]
i. Include NAME, PICTURE, DESIGNATION, and BIO
4. Resources
a. Resources > Patient Health
i. Main Page
1. Posts (ordered by date)
a. Title
b. Summary
2. Side Navigation
a. Post Categories
ii. Patient Health > [post title]
1. Title
2. Post Category
3. Date
4. Author
5. Summary
6. Body
b. Resources > Links
1. Secondary Navigation - Categories
a. Sample Categories:
i. Local Services
ii. RDA and Drug Coverage
iii. Mental Health Resources
2. Category page
a. Include the following links in the 'Local Services' category
i. Hypertension clinics
ii. Home Care services
iii. Vaccine Clinics
c. Resources > Forms
i. Display a table with form TITLE and CATEGORY
ii. Side Navigation
1. Form Categories
a. Use the following sample Categories
i. Referrals
ii. Insurance
iii. Intake
iv. Discharge
v. Waivers
5. Alerts
a. Main page
i. List of all Alert posts
1. Include post TITLE as a link to the post
ii. Side Navigation
1. Alerts Archive
a. shown as Month + Number of posts
iii. Alerts > [Alert page]
1. Include TITLE, DATE, AUTHOR, BODY
6. Contact Us
a. Map
b. Hours of operation
c. Address
d. Phone number
e. Fax number
e. Fax number
f. Map
g. Email

Design notes:
- fixed width
- responsive (need designs for mobile, tablet, and desktop)
- simple, dark font, white background
- use Font Awesome icons where needed
- user adds own logo

Target Market(s)

Medical Clinics

Industry/Entity Type

Medical

Number of Pages Required

5+ page

Font styles to use
Serif
Sans Serif

Requirements
Must have
• Please keep designs very simple.
• Examples:
• https://www.quolbin.com/install
• http://www.ventrohax.com/company/about-us
• http://brindlequota.org/
• http://www.trosk.com/
Should not have
• Minimal or no use of shadows and gradients

```html
<!DOCTYPE html>
<html lang="en">
<head>
<meta charset="utf-8">
<title>Medical Clinics – Patient Health</title>
<link href="https://fonts.googleapis.com/css2?family=Open+Sans:wght@400;600;700&display=swap" rel="stylesheet">
<style>
:root{
  --blue:#0a8be0;
  --ink:#222;
  --text:#333;
  --muted:#666;
  --rule:#d9d9d9;
  --band:#f7f7f7;
  --field:#f8f8f8;
  --footer:#232323;
  --footer-text:#8a8a8a;
  --footer-head:#9a9a9a;
  --white:#fff;
}
*{box-sizing:border-box;margin:0;padding:0}
html,body{width:1200px;height:1035px;overflow:hidden;background:var(--white)}
body{position:relative;font-family:"Open Sans",Arial,sans-serif;color:var(--text);font-size:10px}
a{color:inherit;text-decoration:none}
ul{list-style:none}

.topbar{position:absolute;left:0;top:0;width:1200px;height:30px;background:var(--blue);color:var(--white);font-size:9.5px}
.topbar .left{position:absolute;left:162px;top:9px}
.topbar .right{position:absolute;right:161px;top:9px}
.topbar .sep{display:inline-block;width:1px;height:14px;background:var(--white);vertical-align:middle;margin:0 4px}

.header{position:absolute;left:0;top:30px;width:1200px;height:83px}
.brand{position:absolute;left:162px;top:22px;display:flex;align-items:center;gap:14px;font-size:21px;font-weight:600;color:var(--ink)}
.brand .dot{width:34px;height:34px;border-radius:50%;background:var(--blue)}
.mainnav{position:absolute;right:161px;top:0;display:flex;height:83px}
.mainnav a{display:flex;align-items:center;padding:0 27px;font-size:10.5px;color:var(--ink)}
.mainnav a.active{background:var(--blue);color:var(--white);padding:0 6px;width:60px;justify-content:center}
.mainnav a:last-child{padding-right:0}

.pagehead{position:absolute;left:0;top:113px;width:1200px;height:59px;background:var(--band)}
.pagehead h1{position:absolute;left:162px;top:15px;font-size:10.5px;font-weight:700;color:var(--ink)}
.pagehead .crumbs{position:absolute;left:162px;top:35px;font-size:9.5px;color:var(--ink)}

.col-head{font-size:10.5px;font-weight:700;color:var(--ink);padding-bottom:6px;border-bottom:1px solid var(--rule)}

.sidebar{position:absolute;left:162px;top:219px;width:201px}
.linklist{margin-top:20px;font-size:9.5px;color:var(--ink)}
.linklist li{position:relative;padding-left:14px;height:22.5px}
.linklist li::before{content:"›";position:absolute;left:0;top:-3px;font-size:13px}
.linklist li.current{color:var(--blue);font-weight:600}
.linklist li.sub{margin-left:27px}

.card{border:1px solid var(--rule);box-shadow:0 0 2px rgba(0,0,0,.08)}
.card-title{background:var(--blue);color:var(--white);font-size:10.5px;font-weight:700;padding:9px 13px;height:33px}
.card-body{padding:9px 14px 14px}
.card-intro{font-size:9.5px;line-height:14px;color:var(--ink)}

.resource-form{margin-top:18px}
.resource-form label{display:block;font-size:9.5px;font-weight:600;color:var(--ink);margin-top:17px;margin-bottom:3px}
.field{height:30px;border:1px solid #e4e4e4;background:var(--field);font-size:8.5px;color:var(--muted);padding:0 14px;display:flex;align-items:center;justify-content:space-between}
.submit{margin-top:14px;width:128px;height:30px;background:var(--blue);color:var(--white);font-weight:700;font-size:10.5px;border:0;border-radius:2px;display:flex;align-items:center;justify-content:center}

.article{position:absolute;left:386px;top:219px;width:428px}
.article h2{font-size:12.5px;font-weight:700;color:var(--ink);line-height:17px;margin-top:18px;padding-bottom:11px;border-bottom:1px solid var(--rule)}
.meta{font-size:8.5px;color:var(--muted);margin-top:8px;display:flex;gap:16px}
.meta b{font-weight:400;color:var(--ink)}
.article p{font-size:9.5px;line-height:15.2px;text-align:justify;color:var(--ink);margin-top:13px}
.article p.lead{font-weight:700;margin-top:11px}

.infobox{position:absolute;left:837px;top:209px;width:202px;height:360px}
.infobox .card-body{padding:9px 14px}
.hours{margin-top:13px;font-size:9.5px;color:var(--ink)}
.hours li{display:flex;justify-content:space-between;height:18px}
.divider{border-top:1px solid var(--rule);margin-top:20px}
.contact-title{font-size:10.5px;font-weight:700;color:var(--ink);margin-top:19px}
.contact{margin-top:7px;font-size:9.5px;color:var(--ink);line-height:15px}
.contact div{display:flex}
.contact dt{width:94px}

.footer{position:absolute;left:0;top:808px;width:1200px;height:227px;background:var(--footer);border-top:4px solid var(--blue);color:var(--footer-text)}
.footer .brand{top:37px;color:var(--white)}
.footer-about{position:absolute;left:162px;top:88px;width:205px;font-size:9px;line-height:13px;color:#d0d0d0}
.fcol{position:absolute;top:35px;font-size:9.5px}
.fcol h3{font-size:12.5px;font-weight:600;color:var(--footer-head);margin-bottom:7px}
.fcol li{height:18px}
.fcol li.on{color:var(--white)}
.fcontact{font-size:9.5px;line-height:15px}
.fcontact div{display:flex}
.fcontact dt{width:90px}
.footer-bottom{position:absolute;left:0;top:188px;width:1200px;border-top:1px solid #3a3a3a;font-size:9.5px}
.footer-bottom .copy{position:absolute;left:162px;top:10px}
.footer-bottom nav{position:absolute;left:463px;top:10px;display:flex;gap:26px}
</style>
</head>
<body>

<div class="topbar">
  <div class="left">To help Here : 555 014 2290 <span class="sep"></span> Email : Hello@ Ferncare.ca</div>
  <div class="right">Book an Appointment <span class="sep"></span> Physician Toolbox</div>
</div>

<header class="header">
  <a class="brand" href="#"><span class="dot"></span>Medical Clinics</a>
  <nav class="mainnav">
    <a href="#">Home</a><a href="#">Our Clinic</a><a href="#">Our Staff</a>
    <a href="#" class="active">Resources</a><a href="#">Alerts</a><a href="#">Contact Us</a>
  </nav>
</header>

<section class="pagehead">
  <h1>RESOURCES</h1>
  <div class="crumbs">HOME / RESOURCES/PATIENT-HEALTH</div>
</section>

<aside class="sidebar">
  <div class="col-head">RESOURCES LINKS</div>
  <ul class="linklist">
    <li class="current">Local Services</li>
    <li class="sub">Hypertension clinics</li>
    <li class="sub">Home Care services</li>
    <li class="sub">Vaccine Clinics</li>
    <li>RDA and Drug Coverage</li>
    <li>Mental Health Resources</li>
  </ul>
  <div class="card resource-form">
    <div class="card-title">RESOURCE FORM</div>
    <div class="card-body">
      <p class="card-intro">Lorem Ipsum is simply dummy text of the printing and typesetting</p>
      <label>Title:</label>
      <div class="field"></div>
      <label>Category:</label>
      <div class="field">Select Category:
        <svg width="8" height="5" viewBox="0 0 8 5"><path d="M1 1l3 3 3-3" fill="none" stroke="#555" stroke-width="1"/></svg>
      </div>
      <div class="submit">Submit</div>
    </div>
  </div>
</aside>

<main class="article">
  <div class="col-head">PATIENT HEALTH</div>
  <h2>Lorem Ipsum is simply dummy text of the printing and typesetting industry.</h2>
  <div class="meta"><span>Author : <b>admin</b></span><span>24-June-2015</span><span>Category : <b>Local Services</b></span></div>
  <p class="lead">Contrary to popular belief, Lorem Ipsum is not simply random text. It has roots in a piece of classical Latin literature from 45 BC, making it over 2000 years old. Edmund Harrow, a Latin professor at Wexmoor College in Virginia, looked up one of the more obscure Latin words, consectetur, from a Lorem Ipsum passage, and going through the cites of the word in classical literature,</p>
  <p>Lorem Ipsum is simply dummy text of the printing and typesetting industry. Lorem Ipsum has been the industry's standard dummy text ever since the 1500s, when an unknown printer took a galley of type and scrambled it to make a type specimen book. It has survived not only five centuries, but also the leap into electronic typesetting, remaining essentially unchanged.</p>
  <p>It was popularised in the 1960s with the release of Tremont sheets containing Lorem Ipsum passages, and more recently with desktop publishing software like Pressline Layout including versions of Lorem Ipsum.There are many variations of passages of Lorem Ipsum available, but the majority have suffered alteration in some form, by injected humour, or randomised words which don't look even slightly believable.</p>
  <p>College in Virginia, looked up one of the more obscure Latin words, consectetur, from a Lorem Ipsum passage, and going through the cites of the word in classical literature, discovered the undoubtable source. Lorem Ipsum comes from sections 1.10.32 and 1.10.33 of "de Finibus Bonorum et Malorum" (The Extremes of Good and Evil) by Tullius Varro, written in 45 BC. This book is a treatise on the theory of ethics, very popular during the Renaissance. The first line of Lorem Ipsum, "Lorem ipsum dolor sit amet..", comes from a line in section 1.10.32.</p>
  <p>Discovered the undoubtable source. Lorem Ipsum comes from sections 1.10.32 and 1.10.33 of "de Finibus Bonorum et Malorum" (The Extremes of Good and Evil) by Tullius Varro, written in 45 BC. This book is a treatise on the theory of ethics, very popular during the Renaissance. The first line of Lorem Ipsum, "Lorem ipsum dolor sit amet..", comes from a line in section 1.10.32.</p>
</main>

<aside class="card infobox">
  <div class="card-title">HOURS OF OPRATION</div>
  <div class="card-body">
    <p class="card-intro">Lorem Ipsum is simply dummy text of the printing and typesetting</p>
    <ul class="hours">
      <li><span>Monday :</span><span>8:00 AM - 6:00 PM</span></li>
      <li><span>Tuesday :</span><span>8:00 AM - 6:00 PM</span></li>
      <li><span>Wednesday :</span><span>8:00 AM - 6:00 PM</span></li>
      <li><span>Thursday :</span><span>8:00 AM - 6:00 PM</span></li>
      <li><span>Friday :</span><span>8:00 AM - 6:00 PM</span></li>
      <li><span>Saturday :</span><span>9:00 AM - 4:00 PM</span></li>
      <li><span>Sunday :</span><span>9:00 AM - 4:00 PM</span></li>
    </ul>
    <div class="divider"></div>
    <div class="contact-title">CONTACT INFO</div>
    <dl class="contact">
      <div><dt>Telephone :</dt><dd>555-014-7781</dd></div>
      <div><dt>Email:</dt><dd>hello@ferncare.ca</dd></div>
      <div><dt>Address:</dt><dd>48 Cedar Row<br>Harlow Bay,<br>Canada, H0H 0H0</dd></div>
    </dl>
  </div>
</aside>

<footer class="footer">
  <a class="brand" href="#"><span class="dot"></span>Medical Clinics</a>
  <p class="footer-about">Lorem Ipsum is simply dummy text of the printing and typesetting industry. Lorem Ipsum has been the industry's standard dummy text</p>
  <div class="fcol" style="left:461px">
    <h3>Navigation</h3>
    <ul><li class="on">Home</li><li>Our Clinic</li><li>Newsletter</li><li>Our Staff</li><li>Resources</li></ul>
  </div>
  <div class="fcol" style="left:686px">
    <h3>Links</h3>
    <ul><li>Help</li><li>Support</li><li>Privacy Policy</li></ul>
  </div>
  <div class="fcol" style="left:837px">
    <h3>Contact Us</h3>
    <dl class="fcontact">
      <div><dt>Telephone :</dt><dd>555-014-7781</dd></div>
      <div><dt>Email:</dt><dd>hello@ferncare.ca</dd></div>
      <div><dt>Address:</dt><dd>48 Cedar Row<br>Harlow Bay, Canada,<br>H0H 0H0</dd></div>
    </dl>
  </div>
  <div class="footer-bottom">
    <span class="copy">© 2015 Medical Clinces. All Rights Reservsd</span>
    <nav><a href="#">About Us</a><a href="#">Terms of Use</a><a href="#">Privacy Policy</a></nav>
  </div>
</footer>

</body>
</html>
```